Flat bootstrap design for existing site

I'm looking for a modern flat design based around an existing logo. This has to be a custom design (no external templates), and implemented into a bootstrap framework.

The logo is attached as 2 versions - choose whichever you want, that flows better with whatever design you choose.

Added screenshots of the existing site (currently using the default bootstrap layouts). Please make your designs around those pages in the screenshots (i.e. the homepage only has the postal code input and the header). The active page has 3 screenshots, because I wanted to illustrate the other states that would be visible (in the table rows).

This is a moving/junk removal website, just for some context.

Here's some example websites (flat designs) that I like, just to give you an idea of what I'm after.

https://www.plimvora.com/
https://dacklow.com/
https://trevanu.com/
https://quobrintal.com/en/

Coding

Coded - Design and coding required

Number of Pages Required

5+ page

Colors

Designer to choose colors to be used in the design.

Requirements
Must have
• It must be a modern/simple flat design, that is built around the existing logo (attached).
• It has to be implemented using bootstrap.

```html
<!DOCTYPE html>
<html lang="en">
<head>
<meta charset="utf-8">
<title>Haulvane – Booking Details</title>
<link href="https://fonts.googleapis.com/css2?family=Raleway:wght@400;500;600;700;800&display=swap" rel="stylesheet">
<style>
:root{
  --brand:#55c9f2;
  --brand-dark:#44bfee;
  --ink:#333740;
  --muted:#5b5f66;
  --line:#e7e7e7;
  --panel:#f7f7f7;
  --white:#ffffff;
  --green:#7dc96a;
  --blue:#3a79b8;
  --grey:#7a7a7c;
}
*{box-sizing:border-box;margin:0;padding:0}
html,body{width:1200px;height:1009px;overflow:hidden;background:var(--white);font-family:"Raleway",sans-serif;color:var(--ink)}
.page{position:relative;width:1200px;height:1009px}
.site-header{position:absolute;left:0;top:0;width:1200px;height:75px;background:var(--brand)}
.brand{position:absolute;left:99px;top:20px;display:flex;align-items:center;gap:8px;color:var(--white);font-weight:800;font-size:30px;letter-spacing:1px}
.brand-dot{width:16px;height:16px;border-radius:50%;background:var(--white)}
.nav{position:absolute;top:0;left:0;height:75px;width:1200px}
.nav a{position:absolute;top:0;height:75px;line-height:72px;color:var(--white);text-decoration:none;font-size:13.5px;font-weight:500}
.nav .active{background:var(--white);color:var(--brand);text-align:center;width:158px;left:777px}
.nav .account{left:958px;font-weight:600}
.nav .account svg{vertical-align:middle;margin-left:4px}
.booking{position:absolute;left:99px;top:99px;width:1002px;height:384px;background:var(--panel);border:1px solid var(--line)}
.booking h2{position:absolute;left:27px;top:29px;font-size:15.5px;font-weight:600;letter-spacing:.2px}
.booking hr{position:absolute;left:27px;top:62px;width:939px;border:0;border-top:1px solid var(--line)}
.label{position:absolute;font-size:14.5px;color:var(--muted)}
.field{position:absolute;height:46px;background:var(--white);border:1px solid var(--line);border-radius:2px;font-size:12.5px;color:var(--muted);padding:0 20px;line-height:45px}
.field svg{position:absolute;right:18px;top:15px}
.btn-update{position:absolute;left:29px;top:306px;width:120px;height:47px;background:var(--brand);color:var(--white);border-radius:2px;font-size:13px;font-weight:700;letter-spacing:1.5px;text-align:center;line-height:47px}
.divider{position:absolute;left:99px;top:514px;width:1002px;border-top:1px solid var(--line)}
.drivers-title{position:absolute;left:99px;top:538px;font-size:15.5px;font-weight:600}
.notice{position:absolute;left:99px;top:577px;width:1002px;height:46px;background:var(--panel);border:1px solid var(--line);font-size:12.5px;color:var(--muted);padding-left:20px;line-height:44px}
.drivers{position:absolute;left:99px;top:640px;width:1002px;border-collapse:collapse}
.drivers th{height:47px;text-align:left;font-size:14.5px;font-weight:600;color:var(--ink);border-bottom:1px solid var(--line)}
.drivers td{height:62px;font-size:13px;color:var(--muted);border-bottom:1px solid var(--line)}
.c1{width:167px}.c2{width:193px}.c3{width:144px}.c4{width:187px}
.badge{display:inline-block;width:111px;height:26px;line-height:26px;text-align:center;color:var(--white);font-size:11.5px;border-radius:2px}
.badge.accepted{background:var(--green)}
.badge.sent{background:var(--blue)}
.badge.pending{background:var(--grey)}
.paid{font-weight:600;color:var(--ink)}
.site-footer{position:absolute;left:0;top:962px;width:1200px;height:47px;background:var(--brand);color:var(--white);text-align:center;line-height:47px;font-size:12.5px}
</style>
</head>
<body>
<div class="page">
  <header class="site-header">
    <div class="brand"><span class="brand-dot"></span>HAULVANE</div>
    <nav class="nav">
      <a style="left:580px">BOOK</a>
      <a style="left:660px">HOW IT WORKS</a>
      <a class="active">BECOME A DRIVER</a>
      <a class="account">marcus@qelvorin.com<svg width="9" height="6" viewBox="0 0 9 6"><path d="M0 0h9L4.5 6z" fill="#fff"/></svg></a>
    </nav>
  </header>

  <section class="booking">
    <h2>BOOKING DETAILS</h2>
    <hr>
    <span class="label" style="left:27px;top:88px">Package Selected :</span>
    <span class="label" style="left:504px;top:88px">Pick-up time selected :</span>
    <div class="field" style="left:29px;top:130px;width:469px">Package 1
      <svg width="9" height="14" viewBox="0 0 9 14"><path d="M0 6h9L4.5 0zM0 8h9l-4.5 6z" fill="#555"/></svg>
    </div>
    <div class="field" style="left:505px;top:130px;width:470px">July 18 at 4:13am
      <svg width="14" height="14" viewBox="0 0 14 14"><rect x="1" y="2" width="12" height="11" fill="none" stroke="#666"/><path d="M1 5h12M4 0v4M10 0v4M1 8h12M1 11h12M4 5v8M7 5v8M10 5v8" stroke="#666"/></svg>
    </div>
    <span class="label" style="left:27px;top:209px">Description</span>
    <div class="field" style="left:29px;top:240px;width:944px">1 large stove</div>
    <div class="btn-update">UPDATE</div>
  </section>

  <div class="divider"></div>
  <h2 class="drivers-title">DRIVERS IN YOUR AREA</h2>
  <div class="notice">Please Stay on this page and be patient,While we contact the drivers and find you one ASAP.</div>

  <table class="drivers">
    <thead><tr><th class="c1">Name</th><th class="c2">Distance (km)</th><th class="c3">Agreed Pick-up time</th><th class="c4"></th><th></th></tr></thead>
    <tbody>
      <tr><td>Dorian Pell</td><td>4.04km away</td><td>July 18 at 4:13am</td><td><span class="badge accepted">Time Accepted</span></td><td class="paid">Payment Made</td></tr>
      <tr><td>Anselm Vray</td><td>5.7km away</td><td>-</td><td><span class="badge sent">Request Sent</span></td><td></td></tr>
      <tr><td>Corwin Hale</td><td>11.13km away</td><td>-</td><td><span class="badge sent">Request Sent</span></td><td></td></tr>
      <tr><td>Bram Ostrey</td><td>11.91km away</td><td>-</td><td><span class="badge pending">Pending</span></td><td></td></tr>
    </tbody>
  </table>

  <footer class="site-footer">© copyright 2017 Haulvane.All Rights Reserved</footer>
</div>
</body>
</html>
```